Business card for a new cabinet shop company named Veloran Cabinets for high end cabinets

Design a business card, thinking dark rich green with colours to speak of high end luxury ie; cream, gold, black possibly

Mitchell Tarrowby
Director Craftsman
Email: info@veloranjoinery-example.com.au
Instagram : @veloran.cabinets

```html
<!DOCTYPE html>
<html lang="en">
<head>
<meta charset="utf-8">
<title>Veloran Cabinets – Business Card</title>
<link href="https://fonts.googleapis.com/css2?family=Poppins:wght@400;500;600&display=swap" rel="stylesheet">
<style>
  :root {
    --backdrop: #0f1512;
    --card: #16291f;
    --card-edge: #1e3529;
    --emboss: #2a4536;
    --gold: #c9a55c;
    --cream: #f1ead9;
    --cream-soft: #ddd5c2;
  }
  * { box-sizing: border-box; margin: 0; padding: 0; }
  html, body {
    width: 1200px;
    height: 800px;
    overflow: hidden;
    background: var(--backdrop);
    font-family: "Poppins", sans-serif;
  }
  .canvas {
    width: 1200px;
    height: 800px;
    display: flex;
    align-items: center;
    justify-content: center;
    gap: 40px;
  }
  .card {
    width: 540px;
    height: 310px;
    border-radius: 22px;
    background: var(--card);
    box-shadow: 0 0 0 1px var(--card-edge);
    position: relative;
    overflow: hidden;
  }

  /* Front */
  .card--front {
    display: flex;
    align-items: center;
    justify-content: center;
  }
  .front-wordmark {
    font-weight: 400;
    font-size: 38px;
    letter-spacing: 0.04em;
    color: var(--emboss);
  }

  /* Back */
  .card--back {
    display: flex;
    align-items: center;
    padding: 0 32px 0 40px;
  }
  .back-brand {
    width: 190px;
    display: flex;
    align-items: center;
    gap: 12px;
  }
  .back-brand__square {
    width: 14px;
    height: 14px;
    background: var(--gold);
    flex: none;
  }
  .back-brand__name {
    font-weight: 500;
    font-size: 22px;
    line-height: 1.25;
    color: var(--cream);
  }
  .details {
    flex: 1;
    padding-left: 18px;
  }
  .details__company {
    font-weight: 500;
    font-size: 17px;
    letter-spacing: 0.02em;
    color: var(--cream);
    margin-bottom: 14px;
  }
  .person {
    border-left: 2px solid var(--gold);
    padding-left: 12px;
    margin-bottom: 16px;
  }
  .person__name {
    font-weight: 600;
    font-size: 20px;
    line-height: 1.2;
    color: var(--cream);
  }
  .person__role {
    font-weight: 400;
    font-size: 12px;
    color: var(--gold);
  }
  .contacts {
    list-style: none;
    display: flex;
    flex-direction: column;
    gap: 6px;
  }
  .contacts__item {
    display: flex;
    align-items: center;
    gap: 9px;
    font-size: 11px;
    color: var(--cream-soft);
    white-space: nowrap;
  }
  .contacts__icon {
    width: 12px;
    height: 12px;
    flex: none;
  }
</style>
</head>
<body>
<main class="canvas">
  <section class="card card--front" aria-label="Card front">
    <p class="front-wordmark">Veloran Cabinets</p>
  </section>

  <section class="card card--back" aria-label="Card back">
    <div class="back-brand">
      <span class="back-brand__square"></span>
      <span class="back-brand__name">Veloran<br>Cabinets</span>
    </div>
    <div class="details">
      <p class="details__company">VELORAN CABINETS</p>
      <div class="person">
        <p class="person__name">Mitchell Tarrowby</p>
        <p class="person__role">Director Craftsman</p>
      </div>
      <ul class="contacts">
        <li class="contacts__item">
          <svg class="contacts__icon" viewBox="0 0 12 12" aria-hidden="true">
            <rect x="0.5" y="2.5" width="11" height="7" fill="var(--gold)"/>
            <path d="M0.5 2.5 6 6.5l5.5-4" fill="none" stroke="var(--card)" stroke-width="1"/>
          </svg>
          info@veloranjoinery-example.com.au
        </li>
        <li class="contacts__item">
          <svg class="contacts__icon" viewBox="0 0 12 12" aria-hidden="true">
            <circle cx="6" cy="6" r="5" fill="var(--gold)"/>
          </svg>
          @veloran.cabinets
        </li>
      </ul>
    </div>
  </section>
</main>
</body>
</html>
```